Letterhead, stationery and email signature for construction business

I need the letterhead, stationery and email signature designs for a construction business. I want them to have a corporate feel to them.

I've attached the logo for reference.

```html
<!DOCTYPE html>
<html lang="en">
<head>
<meta charset="utf-8">
<title>Brenmoor Projects – Business Card</title>
<link rel="stylesheet" href="https://fonts.googleapis.com/css2?family=Raleway:wght@700;800&family=Roboto:wght@400;500&display=swap">
<style>
  :root {
    --backdrop: #9a9a9a;
    --paper: #f6f6f4;
    --brand-blue: #3b64b3;
    --card-blue: #2447a0;
    --card-blue-light: #7f97d1;
    --ink-grey: #5f5f63;
    --text-grey: #707074;
  }
  * { box-sizing: border-box; margin: 0; padding: 0; }
  html, body { width: 1200px; height: 970px; overflow: hidden; }
  body {
    background: var(--backdrop);
    position: relative;
    font-family: "Roboto", Arial, sans-serif;
  }
  .card {
    position: absolute;
    left: 300px;
    width: 600px;
    height: 343px;
    border-radius: 3px;
    box-shadow: 0 10px 28px rgba(0,0,0,0.18);
  }
  .card-front { top: 95px; background: var(--paper); }
  .card-back { top: 532px; background: var(--card-blue); }

  .edge-tab {
    position: absolute;
    left: 0;
    top: 112px;
    width: 22px;
    height: 44px;
    background: var(--brand-blue);
  }
  .contact-block {
    position: absolute;
    left: 58px;
    top: 112px;
    color: var(--text-grey);
  }
  .person-name {
    font-family: "Raleway", Arial, sans-serif;
    font-weight: 800;
    font-size: 29px;
    color: var(--brand-blue);
    line-height: 1;
    white-space: nowrap;
  }
  .person-title {
    font-family: "Raleway", Arial, sans-serif;
    font-weight: 700;
    font-size: 15px;
    color: var(--ink-grey);
    margin-top: 4px;
  }
  .address {
    font-size: 16px;
    line-height: 1.3;
    margin-top: 16px;
    width: 270px;
  }
  .contact-rows {
    display: flex;
    align-items: stretch;
    margin-top: 18px;
    font-size: 16px;
  }
  .contact-col { display: flex; flex-direction: column; gap: 6px; }
  .contact-line { display: flex; align-items: center; gap: 8px; white-space: nowrap; }
  .contact-line svg { width: 17px; height: 17px; flex: none; }
  .divider {
    width: 1.5px;
    background: var(--brand-blue);
    margin: 0 16px;
  }

  .wordmark {
    position: absolute;
    display: flex;
    align-items: center;
    font-family: "Raleway", Arial, sans-serif;
    font-weight: 800;
    line-height: 1;
    white-space: nowrap;
  }
  .wordmark-square { flex: none; }
  .wordmark-text { display: flex; flex-direction: column; }
  .wordmark-main { letter-spacing: 0.01em; }
  .wordmark-sub { letter-spacing: 0.5em; }

  .card-front .wordmark { right: 44px; top: 62px; color: var(--brand-blue); gap: 12px; }
  .card-front .wordmark-square { width: 44px; height: 44px; background: var(--brand-blue); }
  .card-front .wordmark-main { font-size: 30px; }
  .card-front .wordmark-sub { font-size: 12px; margin-top: 4px; }

  .card-back .wordmark {
    left: 50%;
    top: 50%;
    transform: translate(-50%, -50%);
    color: var(--card-blue-light);
    gap: 20px;
  }
  .card-back .wordmark-square { width: 80px; height: 80px; background: var(--card-blue-light); }
  .card-back .wordmark-main { font-size: 60px; }
  .card-back .wordmark-sub { font-size: 22px; margin-top: 6px; }
</style>
</head>
<body>
  <section class="card card-front">
    <div class="edge-tab"></div>
    <div class="contact-block">
      <h1 class="person-name">Daniel Harper</h1>
      <p class="person-title">President</p>
      <p class="address">Ashby House, 14 Mercer Road, London SE4 1PL</p>
      <div class="contact-rows">
        <div class="contact-col">
          <p class="contact-line">
            <svg viewBox="0 0 24 24" aria-hidden="true"><path fill="#3b64b3" d="M6.6 10.8a15.1 15.1 0 0 0 6.6 6.6l2.2-2.2c.3-.3.7-.4 1-.2 1.1.4 2.3.6 3.6.6.6 0 1 .4 1 1V20c0 .6-.4 1-1 1A17 17 0 0 1 3 4c0-.6.4-1 1-1h3.5c.6 0 1 .4 1 1 0 1.2.2 2.4.6 3.6.1.3 0 .7-.2 1z"/></svg>
            (555) 318-4400
          </p>
          <p class="contact-line">
            <svg viewBox="0 0 24 24" aria-hidden="true"><path fill="#3b64b3" d="M6 3h12v5H6zM4 9h16a2 2 0 0 1 2 2v6h-4v4H6v-4H2v-6a2 2 0 0 1 2-2zm4 7v3h8v-3z"/></svg>
            (555) 318-4417
          </p>
        </div>
        <div class="divider"></div>
        <div class="contact-col">
          <p class="contact-line">
            <svg viewBox="0 0 24 24" aria-hidden="true"><rect x="2.5" y="5" width="19" height="14" fill="none" stroke="#3b64b3" stroke-width="1.8"/><path d="M3 6l9 7 9-7" fill="none" stroke="#3b64b3" stroke-width="1.8"/></svg>
            info@brenmoor.com
          </p>
          <p class="contact-line">
            <svg viewBox="0 0 24 24" aria-hidden="true"><g fill="none" stroke="#3b64b3" stroke-width="1.6"><circle cx="12" cy="12" r="9"/><ellipse cx="12" cy="12" rx="4" ry="9"/><path d="M3 12h18M5 7h14M5 17h14"/></g></svg>
            www.brenmoor.com
          </p>
        </div>
      </div>
    </div>
    <div class="wordmark">
      <span class="wordmark-square"></span>
      <span class="wordmark-text">
        <span class="wordmark-main">BRENMOOR</span>
        <span class="wordmark-sub">PROJECTS</span>
      </span>
    </div>
  </section>

  <section class="card card-back">
    <div class="wordmark">
      <span class="wordmark-square"></span>
      <span class="wordmark-text">
        <span class="wordmark-main">BRENMOOR</span>
        <span class="wordmark-sub">PROJECTS</span>
      </span>
    </div>
  </section>
</body>
</html>
```